KTWG application splash screen

We need a 1024x768 image for use as an application splash screen.
The image will be displayed full screen on an 10 inch industrial PC 1024x768 screen while our application is launching. The image should convey that the application is "Waiting for connection to Wi-Fi access point..." and include a graphic of the industrial PC connected to the access point via an Ethernet cable. A list of troubleshooting steps should be included at the bottom of the image. The troubleshooting steps should not be the main focus of the image and should be shown in a smaller font (but still readable at 1024x768 displayed on a 10 inch screen).
I will include a mock up of the general idea of what we are looking for as well as image files for the industrial PC, a screenshot of our application to show on the PC's screen and the AP.
For general look and feel and a sense of corporate branding please review our website https://marrowgatesoilworks.example/. The splash screen should reflect corporate branding.
Target Market(s)
Users of our application
Industry/Entity Type
Agriculture
Look and feel

```html
<!DOCTYPE html>
<html lang="en">
<head>
<meta charset="utf-8">
<title>KTWG – Waiting for Wi-Fi access point</title>
<link rel="stylesheet" href="https://fonts.googleapis.com/css2?family=Barlow:wght@400;500;600;700&display=swap">
<style>
  :root {
    --brand-green: #2ab673;
    --white: #ffffff;
    --cable: #1a1a1a;
    --device-dark: #2b2d30;
    --device-screen: #cfd8d3;
    --ap-light: #eef0f0;
  }
  * { margin: 0; padding: 0; box-sizing: border-box; }
  html, body {
    width: 1200px; height: 900px; overflow: hidden;
    background: var(--white);
    font-family: "Barlow", Arial, sans-serif;
  }
  .splash {
    position: relative;
    width: 1024px; height: 768px;
    transform: scale(1.171875);
    transform-origin: 0 0;
    overflow: hidden;
    background: var(--white);
  }
  .backdrop { position: absolute; inset: 0; }
  .headline {
    position: absolute; left: 40px; top: 38px; width: 630px;
    text-align: center; color: var(--white);
    font-weight: 500; font-size: 62px; line-height: 72px;
    letter-spacing: 0.5px;
  }
  .app-tile {
    position: absolute; left: 798px; top: 142px; width: 148px; height: 148px;
    border-radius: 26px; background: var(--brand-green);
    box-shadow: 0 0 0 3px rgba(255,255,255,0.9);
    display: flex; align-items: center; justify-content: center;
    color: var(--white); font-weight: 700; font-size: 40px; letter-spacing: 1px;
  }
  .pc-image {
    position: absolute; left: 86px; top: 326px; width: 270px; height: 216px;
    border-radius: 12px;
    background: linear-gradient(160deg, #3a3c40, var(--device-dark));
  }
  .pc-image .screen {
    position: absolute; left: 22px; top: 20px; right: 22px; bottom: 40px;
    border-radius: 3px;
    background: linear-gradient(180deg, #e9eeeb, var(--device-screen));
  }
  .pc-label {
    position: absolute; left: 89px; top: 548px;
    color: var(--brand-green); font-weight: 500; font-size: 26px;
  }
  .cable-label {
    position: absolute; left: 500px; top: 470px;
    color: var(--brand-green); font-weight: 500; font-size: 23px;
  }
  .ap-image {
    position: absolute; left: 858px; top: 322px; width: 40px; height: 252px;
    border-radius: 12px;
    background: linear-gradient(90deg, #d9dcdc, var(--ap-light) 45%, #d4d7d7);
  }
  .ap-label {
    position: absolute; left: 810px; top: 627px; width: 136px;
    text-align: center; color: var(--white);
    font-weight: 600; font-size: 16.5px; line-height: 18px;
  }
  .ap-label .model { margin-top: 8px; font-size: 15.5px; }
  .troubleshooting {
    position: absolute; left: 45px; top: 622px; width: 740px;
    color: var(--white); font-size: 12.5px; line-height: 16px;
  }
  .troubleshooting h2 { font-size: 12.5px; font-weight: 700; margin-bottom: 8px; }
  .troubleshooting ul { list-style: none; }
  .troubleshooting .step::before { content: "➤"; display: inline-block; width: 17px; }
  .troubleshooting .sub { padding-left: 37px; }
  .troubleshooting .sub li::before { content: "➡"; display: inline-block; width: 13px; margin-left: -13px; font-size: 10px; }
</style>
</head>
<body>
<main class="splash">
  <svg class="backdrop" viewBox="0 0 1024 768" width="1024" height="768" aria-hidden="true">
    <path d="M0 0 H1024 V100 H800 C760 100 740 112 715 145 L640 260 C625 282 612 292 585 292 H0 Z" fill="var(--brand-green)"/>
    <path d="M0 598 H240 L268 626 H1024 V768 H0 Z" fill="var(--brand-green)"/>
    <rect x="800" y="305" width="155" height="417" fill="var(--brand-green)"/>
    <rect x="808" y="316" width="140" height="298" fill="var(--white)"/>
    <rect x="807" y="620" width="142" height="96" fill="none" stroke="var(--white)" stroke-width="2"/>
    <path d="M355 507 H745 C765 507 776 520 776 540 V590 C776 605 788 614 803 614 H858 C872 614 878 600 878 575"
          fill="none" stroke="var(--cable)" stroke-width="4" stroke-linecap="round"/>
  </svg>

  <h1 class="headline">Waiting for connection to Wi-Fi access point...</h1>

  <div class="app-tile">KTWG</div>

  <div class="pc-image" role="img" aria-label="Tractor cab industrial computer showing the KTWG seeding application">
    <div class="screen"></div>
  </div>
  <p class="pc-label">Tractor Cab Computer</p>

  <p class="cable-label">Ethernet Cable</p>

  <div class="ap-image" role="img" aria-label="Outdoor Wi-Fi access point with two antennas"></div>
  <div class="ap-label">
    <p>Wi-Fi Access Point</p>
    <p class="model">Relaynet RX300-Outdoor</p>
  </div>

  <section class="troubleshooting">
    <h2>Troubleshooting steps:</h2>
    <ul>
      <li class="step">This screen should only be visible for a short time on boot.</li>
      <li class="step">If this screen stays visible for more than a minute:
        <ul class="sub">
          <li>Verify that the Wi-Fi Access Point (AP) powers up when this system does (indicated by a green light on the side of the AP).</li>
          <li>Check the Ethernet cable between this system and the AP for damage, and replace it if necessary.</li>
          <li>Power-cycle this system and wait for it to reboot fully.</li>
          <li>If the issue persists, contact KTWG support for further assistance.</li>
        </ul>
      </li>
    </ul>
  </section>
</main>
</body>
</html>
```